Business Card for a Dental Office

The design should communicate integrity, quality and reliability. We also want the card look elegant, simple, but still stand out, different from the traditional-dental-office business card.

Industry/Entity Type

Business

```html
<!DOCTYPE html>
<html lang="en">
<head>
<meta charset="utf-8">
<title>Harwell Dental Studio – Business Card</title>
<link href="https://fonts.googleapis.com/css2?family=Oswald:wght@500;700&family=Open+Sans:wght@400;700&display=swap" rel="stylesheet">
<style>
  :root {
    --backdrop: #e9e6e1;
    --card: #ffffff;
    --ink: #141414;
    --gold: #a8863f;
    --gold-bright: #c9a227;
    --muted: #3a3a3a;
  }
  * { margin: 0; padding: 0; box-sizing: border-box; }
  html, body {
    width: 1200px; height: 1022px; overflow: hidden;
    background: var(--backdrop);
  }
  .card {
    position: absolute; left: 100px; top: 225px;
    width: 1000px; height: 572px;
    background: var(--card);
    box-shadow: 0 10px 30px rgba(0,0,0,0.18);
  }
  .brand {
    position: absolute; left: 70px; top: 78px;
    display: flex; align-items: center; gap: 22px;
  }
  .brand-mark {
    width: 74px; height: 74px; background: var(--gold-bright); flex: none;
  }
  .brand-name {
    font-family: "Oswald", sans-serif; font-weight: 700;
    font-size: 52px; line-height: 1; letter-spacing: 0.5px;
    color: var(--ink); text-transform: uppercase; white-space: nowrap;
  }
  .brand-tagline {
    font-family: "Oswald", sans-serif; font-weight: 500;
    font-size: 22px; line-height: 1; margin-top: 6px;
    letter-spacing: 1px; color: var(--gold-bright); text-transform: uppercase;
    white-space: nowrap;
  }
  .person {
    position: absolute; right: 70px; top: 300px; text-align: right;
  }
  .person-name {
    font-family: "Open Sans", sans-serif; font-weight: 700;
    font-size: 42px; line-height: 1; color: var(--ink); text-transform: uppercase;
    white-space: nowrap;
  }
  .person-title {
    font-family: "Open Sans", sans-serif; font-weight: 400;
    font-size: 20px; letter-spacing: 3px; margin-top: 8px;
    color: var(--gold); text-transform: uppercase;
  }
  .divider {
    position: absolute; left: 70px; right: 70px; top: 408px;
    height: 3px; background: var(--gold);
  }
  .contacts {
    position: absolute; left: 70px; top: 428px;
    list-style: none;
    font-family: "Open Sans", sans-serif; font-size: 23px;
    color: var(--muted);
  }
  .contacts li { display: flex; align-items: center; gap: 14px; height: 38px; white-space: nowrap; }
  .contacts svg { width: 20px; height: 20px; flex: none; }
</style>
</head>
<body>
  <main class="card">
    <div class="brand">
      <span class="brand-mark"></span>
      <div>
        <div class="brand-name">Harwell Dental Studio</div>
        <div class="brand-tagline">Gentle care you can rely on daily</div>
      </div>
    </div>

    <div class="person">
      <div class="person-name">Daniel Reyes</div>
      <div class="person-title">Director</div>
    </div>

    <div class="divider"></div>

    <ul class="contacts">
      <li>
        <svg viewBox="0 0 24 24" aria-hidden="true"><path fill="var(--gold)" d="M6.6 10.8a15 15 0 0 0 6.6 6.6l2.2-2.2c.3-.3.7-.4 1-.2 1.1.4 2.3.6 3.6.6.6 0 1 .4 1 1V20c0 .6-.4 1-1 1A17 17 0 0 1 3 4c0-.6.4-1 1-1h3.5c.6 0 1 .4 1 1 0 1.3.2 2.5.6 3.6.1.3 0 .7-.2 1z"/></svg>
        <span>+100 5550-4821</span>
      </li>
      <li>
        <svg viewBox="0 0 24 24" aria-hidden="true"><rect x="2.5" y="5" width="19" height="14" fill="none" stroke="var(--gold)" stroke-width="2"/><path d="M3 6l9 7 9-7" fill="none" stroke="var(--gold)" stroke-width="2"/></svg>
        <span>hello@harwelldentalstudio.com</span>
      </li>
      <li>
        <svg viewBox="0 0 24 24" aria-hidden="true"><g fill="none" stroke="var(--gold)" stroke-width="2"><circle cx="12" cy="12" r="9.5"/><path d="M2.5 12h19M12 2.5c3 3 3 16 0 19M12 2.5c-3 3-3 16 0 19"/></g></svg>
        <span>www.harwelldentalstudio.com</span>
      </li>
    </ul>
  </main>
</body>
</html>
```